I work in creative/artistic projects across different mediums.
It needs to communicate creativity, style, sexy, uniqueness, individuality and sophistication.
It should not look corporate.
Colours I like are black silver gold deep purple, chocolate, orchid.
It doesn't have to make use of all these colours.
I do not like bright primary colors.
Updates

Project Deadline Extended
Reason: Still in the communication process and to allow the person enough time to finish the design. Though i should know in the next day or two. Thank you.

Target Market(s)

creatives and companies wanting to inject creativity into thier business.

Industry/Entity Type

Work

Contact Information for Business Card

Corwin Haldley
0418592036
corwin@corwinhaldley-example.com

quietgoldenhourstudio.example.au

Requirements
Should not have
• Anything corporate OR OLD FASHIONED

```html
<!DOCTYPE html>
<html lang="en">
<head>
<meta charset="utf-8">
<title>Corwin Haldley – Business Card</title>
<link rel="stylesheet" href="https://fonts.googleapis.com/css2?family=Arimo:wght@700&display=swap">
<style>
  :root {
    --backdrop: #2b2630;
    --violet-deep: #3b1f5e;
    --violet-mid: #6a47a0;
    --violet-glow: #cfc3e6;
    --ink: #2a1545;
    --label-bg: #3a1d58;
    --label-text: #d9cdef;
    --band-dark: #301a4f;
  }
  html, body {
    margin: 0;
    width: 1200px;
    height: 1000px;
    overflow: hidden;
    background: var(--backdrop);
  }
  .stage {
    width: 1200px;
    height: 1000px;
    display: flex;
    align-items: center;
    justify-content: center;
  }
  .card {
    position: relative;
    width: 900px;
    height: 514px;
    overflow: hidden;
    border-radius: 4px;
    background:
      radial-gradient(ellipse 48% 60% at 52% 48%, var(--violet-glow) 0%, #a58fcb 35%, var(--violet-mid) 70%, var(--violet-deep) 100%);
    box-shadow: 0 20px 50px rgba(0,0,0,.45);
    font-family: "Arimo", Arial, sans-serif;
    font-weight: 700;
  }
  .name-label {
    position: absolute;
    top: 46px;
    right: 46px;
    margin: 0;
    padding: 10px 18px 8px;
    background: var(--label-bg);
    color: var(--label-text);
    font-size: 40px;
    letter-spacing: 2px;
    text-transform: uppercase;
    line-height: 1;
  }
  .contact-list {
    position: absolute;
    left: 100px;
    top: 190px;
    margin: 0;
    padding: 0;
    list-style: none;
  }
  .contact-item {
    display: flex;
    align-items: center;
    height: 62px;
    color: var(--ink);
    font-size: 30px;
  }
  .contact-icon {
    width: 38px;
    height: 38px;
    margin-right: 26px;
    flex: none;
  }
  .divider-band {
    position: absolute;
    left: 0;
    right: 0;
    bottom: 0;
    height: 96px;
    background: linear-gradient(180deg, rgba(48,26,79,.55), var(--band-dark));
    border-top: 8px solid var(--ink);
  }
</style>
</head>
<body>
<main class="stage">
  <section class="card" aria-label="Business card for Corwin Haldley">
    <h1 class="name-label">Corwin Haldley</h1>
    <ul class="contact-list">
      <li class="contact-item">
        <svg class="contact-icon" viewBox="0 0 38 38" aria-hidden="true">
          <rect x="3" y="8" width="32" height="22" fill="var(--ink)"/>
          <path d="M3 8 L19 21 L35 8" fill="none" stroke="#b9a6da" stroke-width="2"/>
          <path d="M3 30 L15 18 M35 30 L23 18" stroke="#b9a6da" stroke-width="1.5"/>
        </svg>
        corwin@corwinhaldley-example.com
      </li>
      <li class="contact-item">
        <svg class="contact-icon" viewBox="0 0 38 38" aria-hidden="true">
          <rect x="10" y="3" width="18" height="32" rx="3" fill="none" stroke="var(--ink)" stroke-width="3"/>
          <line x1="16" y1="30" x2="22" y2="30" stroke="var(--ink)" stroke-width="2"/>
        </svg>
        0418592036
      </li>
      <li class="contact-item">
        <svg class="contact-icon" viewBox="0 0 38 38" aria-hidden="true">
          <circle cx="19" cy="19" r="15" fill="var(--ink)"/>
          <g fill="none" stroke="#b9a6da" stroke-width="1.5">
            <ellipse cx="19" cy="19" rx="6" ry="15"/>
            <line x1="19" y1="4" x2="19" y2="34"/>
            <line x1="4" y1="19" x2="34" y2="19"/>
            <path d="M7 11 H31 M7 27 H31"/>
          </g>
        </svg>
        quietgoldenhourstudio.example.au
      </li>
    </ul>
    <div class="divider-band"></div>
  </section>
</main>
</body>
</html>
```